Business Cards for company that supports physicians that do medical research

Need to create a business card for Qorvel Studies (www.qorvelstudies.example), a company devoted to supporting physicians who conduct medical research. The form of the card should match the message of research and information quest. I have provided the logo of the company as an uploaded file. Designs should be simple and slick aimed at very high end clients.

Target Market(s)

Medical doctors that are also researchers

Industry/Entity Type

Medical

Contact Information for Business Card

Should feature logo and fields for personal info:
Name/title
Phone /email

Font styles to use
Serif
Sans Serif

Requirements
Must have
• Qorvel logo and fields for personal info:
• Name: Bertrand Okonfu
• Title: VP Research and Senior Analyst
• Phone: 555-203-4719
• email: info@qorvelstudies.example
Nice to have
• Interesting cards that I've seen:
• 1- all black/charcoal or very dark background
• 2- Plastic - semi-transparent
• 3- non-standard height-width ratios
• 4- Functional cards -- USB drive incorporated
Should not have
• Too busy; needs to stay very simple

```html
<!DOCTYPE html>
<html lang="en">
<head>
<meta charset="utf-8">
<title>Qorvel Studies – Business Card</title>
<link rel="stylesheet" href="https://fonts.googleapis.com/css2?family=Oswald:wght@500;600&family=Tinos&display=swap">
<style>
  :root {
    --page-bg: #2a2a2c;
    --card-black: #0d0d0e;
    --clear-panel: #8e8f91;
    --clear-panel-light: #b4b5b7;
    --gold: #c9a54e;
    --gold-light: #e3c77c;
    --gold-dark: #8f7130;
  }
  html, body {
    margin: 0;
    padding: 0;
    width: 1200px;
    height: 880px;
    overflow: hidden;
    background: var(--page-bg);
  }
  .business-card {
    position: absolute;
    left: 110px;
    top: 130px;
    width: 980px;
    height: 620px;
    background: var(--card-black);
    border-radius: 22px;
    overflow: hidden;
    box-shadow: 0 20px 50px rgba(0,0,0,0.55);
  }
  .clear-panel {
    position: absolute;
    left: 410px;
    top: 0;
    right: 0;
    height: 520px;
    border-top-left-radius: 70px;
    border-bottom-left-radius: 70px;
    background: linear-gradient(160deg, var(--clear-panel-light), var(--clear-panel));
    opacity: 0.9;
  }
  .person-name {
    position: absolute;
    left: 36px;
    top: 44px;
    width: 360px;
    margin: 0;
    font-family: "Oswald", sans-serif;
    font-weight: 600;
    font-size: 40px;
    letter-spacing: 1px;
    line-height: 1;
    color: var(--gold);
    white-space: nowrap;
    text-align: right;
  }
  .person-title {
    position: absolute;
    left: 36px;
    top: 98px;
    width: 360px;
    margin: 0;
    font-family: "Oswald", sans-serif;
    font-weight: 500;
    font-size: 18px;
    letter-spacing: 1px;
    line-height: 1.2;
    color: var(--gold);
    white-space: nowrap;
    text-align: right;
  }
  .medical-emblem {
    position: absolute;
    left: 80px;
    top: 150px;
  }
  .phone {
    position: absolute;
    left: 40px;
    top: 468px;
    font-family: "Oswald", sans-serif;
    font-weight: 500;
    font-size: 24px;
    color: var(--gold);
  }
  .email {
    position: absolute;
    left: 150px;
    top: 550px;
    font-family: "Tinos", serif;
    font-size: 26px;
    color: var(--gold);
    white-space: nowrap;
  }
  .website {
    position: absolute;
    right: 50px;
    top: 552px;
    font-family: "Tinos", serif;
    font-size: 24px;
    color: var(--gold);
    white-space: nowrap;
  }
  .brand {
    position: absolute;
    left: 460px;
    top: 215px;
    display: flex;
    align-items: center;
    gap: 20px;
    white-space: nowrap;
  }
  .brand-dot {
    width: 36px;
    height: 36px;
    border-radius: 50%;
    background: var(--gold);
    flex: none;
  }
  .brand-name {
    font-family: "Oswald", sans-serif;
    font-weight: 600;
    font-size: 64px;
    letter-spacing: 2px;
    line-height: 1;
    color: var(--gold);
  }
</style>
</head>
<body>
  <div class="business-card">
    <div class="clear-panel"></div>

    <h1 class="person-name">BERTRAND OKONFU</h1>
    <p class="person-title">VP RESEARCH AND SENIOR ANALYST</p>

    <svg class="medical-emblem" width="250" height="280" viewBox="0 0 250 280" role="img" aria-label="Gold winged staff with serpents, medical emblem">
      <defs>
        <linearGradient id="emblemGold" x1="0" y1="0" x2="1" y2="1">
          <stop offset="0" stop-color="#e3c77c"/>
          <stop offset="1" stop-color="#8f7130"/>
        </linearGradient>
      </defs>
      <rect x="0" y="0" width="250" height="280" rx="20" fill="url(#emblemGold)" opacity="0.85"/>
    </svg>

    <div class="phone">555-203-4719</div>

    <div class="brand">
      <span class="brand-dot"></span>
      <span class="brand-name">Qorvel Studies</span>
    </div>

    <div class="email">info@qorvelstudies.example</div>
    <div class="website">www.qorvelstudies.example</div>
  </div>
</body>
</html>
```